Four in One (Flexible infographic for Content Management Industry)

See attachment.
A graphic depicting 4 products, where each can stand on its own and each can be combined with others, but where, if all are taken together, the best result is achieved (the "super product").
Intended use is web. See attached file as an example.
The most basic idea is as the attached diagram shows, where 4 rectangles are arranged in a quadrangle, with a middle rectangle in the center representing the combined 4 products. This concept is fine except it is a bit too obvious as it stands. We are looking for either a variation of this or another concept.
The audience is technical + professional + enterprise - NOT consumers. Hence the design should be conservative in nature.
We are aware of tools like as Canva or Pictogram where such graphics are available, but we are looking for something with a bit more imagination and flexibility.
This graphic should be targeted to web sites and be delivered with vector-based (SVG) graphics.

```html
<!DOCTYPE html>
<html lang="en">
<head>
<meta charset="utf-8">
<title>Four in One – Super Product</title>
<link rel="stylesheet" href="https://fonts.googleapis.com/css2?family=Montserrat:wght@400;500&family=Saira+Semi+Condensed:wght@500;600;800&display=swap">
<style>
  :root {
    --page-bg: #f4f5f6;
    --white: #ffffff;
    --green-a: #1aa560;
    --green-b: #36d293;
    --purple-a: #b65cf2;
    --purple-b: #5b4fd0;
    --purple-c: #15519e;
    --navy-a: #2b3590;
    --navy-b: #0a78cf;
    --teal-a: #0f93b0;
    --teal-b: #06a3bf;
    --core-red: #f4434c;
    --core-red-dark: #e6323e;
    --ring-green: #2cc07f;
    --ring-purple: #8c55e6;
    --ring-navy: #1c4fa8;
    --ring-teal: #0aaad0;
    --rule: rgba(255,255,255,0.45);
    --display: "Saira Semi Condensed", "Arial Narrow", "Roboto Condensed", sans-serif;
    --body: "Montserrat", sans-serif;
  }
  * { margin: 0; padding: 0; box-sizing: border-box; }
  html, body { width: 1200px; height: 927px; overflow: hidden; }
  body {
    background: radial-gradient(ellipse at center, #ffffff 0%, var(--page-bg) 100%);
    position: relative;
    color: var(--white);
    font-family: var(--body);
  }
  .infographic {
    position: absolute; left: 179px; top: 150px;
    width: 843px; height: 628px;
    display: grid; grid-template-columns: 1fr 1fr; grid-template-rows: 1fr 1fr;
  }
  .quadrant { position: relative; }
  .quadrant--document { background: linear-gradient(135deg, var(--green-a) 0%, var(--green-b) 100%); }
  .quadrant--security { background: linear-gradient(225deg, var(--purple-c) 0%, var(--purple-b) 45%, var(--purple-a) 100%); }
  .quadrant--erp { background: linear-gradient(45deg, var(--navy-a) 0%, var(--navy-a) 40%, var(--navy-b) 100%); }
  .quadrant--digital { background: linear-gradient(135deg, var(--teal-a) 0%, var(--teal-b) 100%); }

  .quadrant__title, .quadrant__desc, .features { position: absolute; z-index: 2; }
  .quadrant__title {
    font-family: var(--display);
    font-weight: 800; font-size: 24px; line-height: 29px;
    letter-spacing: 0.2px; text-transform: uppercase; white-space: nowrap;
  }
  .quadrant__desc {
    font-size: 13.4px; line-height: 17.4px; font-weight: 400; white-space: nowrap;
  }
  .features { list-style: none; width: 242px; }
  .features li {
    height: 27px; display: flex; align-items: center; gap: 8px;
    font-family: var(--display);
    font-weight: 500; font-size: 14.6px; letter-spacing: 0.2px;
    border-bottom: 1px solid var(--rule);
    white-space: nowrap;
  }
  .features li:last-child { border-bottom: none; }
  .features li.compact { font-size: 13px; }
  .tick { width: 15px; height: 15px; flex: none; }

  .quadrant--document .quadrant__title,
  .quadrant--erp .quadrant__title,
  .quadrant--document .quadrant__desc,
  .quadrant--erp .quadrant__desc,
  .quadrant--document .features,
  .quadrant--erp .features { left: 31px; }

  .quadrant--security .quadrant__title,
  .quadrant--digital .quadrant__title,
  .quadrant--security .quadrant__desc,
  .quadrant--digital .quadrant__desc { right: 30px; text-align: right; }
  .quadrant--security .features,
  .quadrant--digital .features { right: 28px; }
  .quadrant--security .features li,
  .quadrant--digital .features li { justify-content: flex-end; }

  .quadrant--document .quadrant__title { top: 33px; }
  .quadrant--document .quadrant__desc { top: 108px; }
  .quadrant--document .features { top: 173px; }

  .quadrant--security .quadrant__title { top: 31px; }
  .quadrant--security .quadrant__desc { top: 108px; }
  .quadrant--security .features { top: 173px; width: 190px; }

  .quadrant--erp .quadrant__title { top: 39px; }
  .quadrant--erp .quadrant__desc { top: 120px; }
  .quadrant--erp .features { top: 182px; }

  .quadrant--digital .quadrant__title { top: 39px; }
  .quadrant--digital .quadrant__desc { top: 120px; }
  .quadrant--digital .features { top: 182px; width: 275px; }

  .hub { position: absolute; left: 0; top: 0; width: 1200px; height: 927px; pointer-events: none; z-index: 1; }
  .hub__label {
    position: absolute; left: 486px; top: 443px; width: 230px; text-align: center; z-index: 3;
    font-family: var(--display); font-weight: 800;
    font-size: 23px; line-height: 30px; letter-spacing: 0.2px; color: var(--white); white-space: nowrap;
  }
</style>
</head>
<body>
  <main class="infographic">
    <section class="quadrant quadrant--document">
      <h2 class="quadrant__title">Document<br>Management</h2>
      <p class="quadrant__desc">Streamline document organization, access, and<br>collaboration with easier file storage and sharing,<br>leading to more effecient workflows.</p>
      <ul class="features">
        <li><svg class="tick" viewBox="0 0 16 16"><circle cx="8" cy="8" r="6.8" fill="none" stroke="#fff" stroke-width="1.4"/><path d="M4.8 8.2l2.2 2.2 5-5.4" fill="none" stroke="#fff" stroke-width="1.6" stroke-linecap="round"/></svg>Centralized Document Control</li>
        <li class="compact"><svg class="tick" viewBox="0 0 16 16"><circle cx="8" cy="8" r="6.8" fill="none" stroke="#fff" stroke-width="1.4"/><path d="M4.8 8.2l2.2 2.2 5-5.4" fill="none" stroke="#fff" stroke-width="1.6" stroke-linecap="round"/></svg>Collaborative Workspace Integration</li>
        <li><svg class="tick" viewBox="0 0 16 16"><circle cx="8" cy="8" r="6.8" fill="none" stroke="#fff" stroke-width="1.4"/><path d="M4.8 8.2l2.2 2.2 5-5.4" fill="none" stroke="#fff" stroke-width="1.6" stroke-linecap="round"/></svg>Automated Compliance Tracking</li>
        <li><svg class="tick" viewBox="0 0 16 16"><circle cx="8" cy="8" r="6.8" fill="none" stroke="#fff" stroke-width="1.4"/><path d="M4.8 8.2l2.2 2.2 5-5.4" fill="none" stroke="#fff" stroke-width="1.6" stroke-linecap="round"/></svg>Check 4</li>
      </ul>
    </section>

    <section class="quadrant quadrant--security">
      <h2 class="quadrant__title">Security &amp;<br>Compliance</h2>
      <p class="quadrant__desc">Benefit from tailored cloud solutions, secure data<br>storage, and expert disaster recovery planning for<br>reliable and scalable IT operations.</p>
      <ul class="features">
        <li>Custom cloud Solutions<svg class="tick" viewBox="0 0 16 16"><circle cx="8" cy="8" r="6.8" fill="none" stroke="#fff" stroke-width="1.4"/><path d="M4.8 8.2l2.2 2.2 5-5.4" fill="none" stroke="#fff" stroke-width="1.6" stroke-linecap="round"/></svg></li>
        <li>Secure Data Storage<svg class="tick" viewBox="0 0 16 16"><circle cx="8" cy="8" r="6.8" fill="none" stroke="#fff" stroke-width="1.4"/><path d="M4.8 8.2l2.2 2.2 5-5.4" fill="none" stroke="#fff" stroke-width="1.6" stroke-linecap="round"/></svg></li>
        <li>Expert Disaster Recovery<svg class="tick" viewBox="0 0 16 16"><circle cx="8" cy="8" r="6.8" fill="none" stroke="#fff" stroke-width="1.4"/><path d="M4.8 8.2l2.2 2.2 5-5.4" fill="none" stroke="#fff" stroke-width="1.6" stroke-linecap="round"/></svg></li>
        <li>Check 4<svg class="tick" viewBox="0 0 16 16"><circle cx="8" cy="8" r="6.8" fill="none" stroke="#fff" stroke-width="1.4"/><path d="M4.8 8.2l2.2 2.2 5-5.4" fill="none" stroke="#fff" stroke-width="1.6" stroke-linecap="round"/></svg></li>
      </ul>
    </section>

    <section class="quadrant quadrant--erp">
      <h2 class="quadrant__title">Enterprise<br>Resource Planning</h2>
      <p class="quadrant__desc">Simplify management across finance,<br>sales, and operations, enabling better decision-making<br>and improved productivity.</p>
      <ul class="features">
        <li><svg class="tick" viewBox="0 0 16 16"><circle cx="8" cy="8" r="6.8" fill="none" stroke="#fff" stroke-width="1.4"/><path d="M4.8 8.2l2.2 2.2 5-5.4" fill="none" stroke="#fff" stroke-width="1.6" stroke-linecap="round"/></svg>Integrated Business Processes</li>
        <li><svg class="tick" viewBox="0 0 16 16"><circle cx="8" cy="8" r="6.8" fill="none" stroke="#fff" stroke-width="1.4"/><path d="M4.8 8.2l2.2 2.2 5-5.4" fill="none" stroke="#fff" stroke-width="1.6" stroke-linecap="round"/></svg>Enhanced Decision-Making</li>
        <li><svg class="tick" viewBox="0 0 16 16"><circle cx="8" cy="8" r="6.8" fill="none" stroke="#fff" stroke-width="1.4"/><path d="M4.8 8.2l2.2 2.2 5-5.4" fill="none" stroke="#fff" stroke-width="1.6" stroke-linecap="round"/></svg>Productivity Improvement</li>
        <li><svg class="tick" viewBox="0 0 16 16"><circle cx="8" cy="8" r="6.8" fill="none" stroke="#fff" stroke-width="1.4"/><path d="M4.8 8.2l2.2 2.2 5-5.4" fill="none" stroke="#fff" stroke-width="1.6" stroke-linecap="round"/></svg>Check 4</li>
      </ul>
    </section>

    <section class="quadrant quadrant--digital">
      <h2 class="quadrant__title">Digital<br>Transformation</h2>
      <p class="quadrant__desc">Turn scanned documents into easily<br>searchable digital archives, boosting effeciency<br>and accessibility.</p>
      <ul class="features">
        <li>Instant searchable Archives with OCR<svg class="tick" viewBox="0 0 16 16"><circle cx="8" cy="8" r="6.8" fill="none" stroke="#fff" stroke-width="1.4"/><path d="M4.8 8.2l2.2 2.2 5-5.4" fill="none" stroke="#fff" stroke-width="1.6" stroke-linecap="round"/></svg></li>
        <li>Automated Document Classification<svg class="tick" viewBox="0 0 16 16"><circle cx="8" cy="8" r="6.8" fill="none" stroke="#fff" stroke-width="1.4"/><path d="M4.8 8.2l2.2 2.2 5-5.4" fill="none" stroke="#fff" stroke-width="1.6" stroke-linecap="round"/></svg></li>
        <li>TeamVault and Cloud Blob Ready<svg class="tick" viewBox="0 0 16 16"><circle cx="8" cy="8" r="6.8" fill="none" stroke="#fff" stroke-width="1.4"/><path d="M4.8 8.2l2.2 2.2 5-5.4" fill="none" stroke="#fff" stroke-width="1.6" stroke-linecap="round"/></svg></li>
        <li>Check 4<svg class="tick" viewBox="0 0 16 16"><circle cx="8" cy="8" r="6.8" fill="none" stroke="#fff" stroke-width="1.4"/><path d="M4.8 8.2l2.2 2.2 5-5.4" fill="none" stroke="#fff" stroke-width="1.6" stroke-linecap="round"/></svg></li>
      </ul>
    </section>
  </main>

  <svg class="hub" viewBox="0 0 1200 927">
    <defs>
      <radialGradient id="coreFill" cx="50%" cy="45%" r="60%">
        <stop offset="0%" stop-color="#f75a62"/>
        <stop offset="100%" stop-color="#e6323e"/>
      </radialGradient>
    </defs>
    <circle cx="600" cy="464" r="155" fill="rgba(255,255,255,0.14)"/>
    <circle cx="600" cy="464" r="131" fill="rgba(255,255,255,0.12)"/>
    <circle cx="600" cy="464" r="126" fill="#ffffff"/>
    <path d="M600 342 A122 122 0 0 0 478 464" fill="none" stroke="var(--ring-green)" stroke-width="4"/>
    <path d="M600 342 A122 122 0 0 1 722 464" fill="none" stroke="var(--ring-purple)" stroke-width="4"/>
    <path d="M478 464 A122 122 0 0 0 600 586" fill="none" stroke="var(--ring-navy)" stroke-width="4"/>
    <path d="M722 464 A122 122 0 0 1 600 586" fill="none" stroke="var(--ring-teal)" stroke-width="4"/>
    <circle cx="600" cy="464" r="116" fill="#ffffff"/>
    <circle cx="600" cy="464" r="112" fill="url(#coreFill)" role="img" aria-label="Red circuit-board texture representing the combined super product"/>

    <g class="badge badge--document">
      <circle cx="501" cy="366" r="37" fill="#ffffff"/>
      <circle cx="501" cy="366" r="30" fill="var(--ring-green)"/>
      <path d="M491 352 h10 M489 354 v20 a5 5 0 0 0 5 5 h10 a5 5 0 0 0 5 -5 v-4 M487 374 a4 4 0 0 0 8 0" fill="none" stroke="#fff" stroke-width="2" stroke-linecap="round"/>
      <circle cx="510" cy="359" r="7.5" fill="var(--ring-green)" stroke="#fff" stroke-width="2"/>
      <path d="M506.5 359 l2.5 2.5 4.5 -5" fill="none" stroke="#fff" stroke-width="2" stroke-linecap="round"/>
    </g>
    <g class="badge badge--security">
      <circle cx="699" cy="366" r="37" fill="#ffffff"/>
      <circle cx="699" cy="366" r="30" fill="var(--ring-purple)"/>
      <path d="M687 374 a8 8 0 0 1 1 -16 a11 11 0 0 1 21 2 a7 7 0 0 1 2 14" fill="none" stroke="#fff" stroke-width="2" stroke-linecap="round"/>
      <path d="M699 363 l8 3 v5 c0 5 -4 8 -8 10 c-4 -2 -8 -5 -8 -10 v-5 z" fill="var(--ring-purple)" stroke="#fff" stroke-width="2" stroke-linejoin="round"/>
      <path d="M695.5 371 l2.5 2.5 4.5 -5" fill="none" stroke="#fff" stroke-width="2" stroke-linecap="round"/>
    </g>
    <g class="badge badge--erp">
      <circle cx="501" cy="542" r="37" fill="#ffffff"/>
      <circle cx="501" cy="542" r="30" fill="var(--ring-navy)"/>
      <circle cx="501" cy="542" r="10" fill="none" stroke="#fff" stroke-width="2" stroke-dasharray="4 2.3"/>
      <circle cx="501" cy="542" r="4" fill="none" stroke="#fff" stroke-width="2"/>
      <path d="M486 536 a16 16 0 0 1 25 -9 M516 548 a16 16 0 0 1 -25 9" fill="none" stroke="#fff" stroke-width="2" stroke-linecap="round"/>
    </g>
    <g class="badge badge--digital">
      <circle cx="699" cy="542" r="37" fill="#ffffff"/>
      <circle cx="699" cy="542" r="30" fill="var(--ring-teal)"/>
      <path d="M705 555 h-17 a3 3 0 0 1 -3 -3 v-20 a3 3 0 0 1 3 -3 h21 a3 3 0 0 1 3 3 v8 M685 535 h27" fill="none" stroke="#fff" stroke-width="2" stroke-linecap="round"/>
      <path d="M689 542 h2 M694 542 h6 M689 548 h2 M694 548 h4" stroke="#fff" stroke-width="2" stroke-linecap="round"/>
      <circle cx="707" cy="549" r="4.5" fill="none" stroke="#fff" stroke-width="2"/>
      <path d="M710.5 552.5 l3.5 3.5" stroke="#fff" stroke-width="2" stroke-linecap="round"/>
    </g>
  </svg>
  <div class="hub__label">SUPER PRODUCT</div>
</body>
</html>
```